web page look and feel - B2B enterprise application

We have an enterprise application with 10 to 15 core pages and several supporting pages or popups. To start, we want the graphical design of the Users, Roles and Data Source pages and their supporting popups, wizards, etc. to be made beautiful. That is around 10 pages in total. There is a fair amount of redundancy among the pages. I have attached 5 screenshots. We very much want the pages to project a premium feel. That is absolutely essential. The color scheme is blue and sometimes yellow (only if it makes the page look better) plus black, gray and white. If the design of these screens goes well, we would expand the project to continue with other pages. The core of what we are looking for is graphic in nature but we are open to workflow suggestions if you have them. The Roles screen needs some improvements to the layout. I am looking for everything that includes icons, fonts, spacing, etc. I assume getting to the final design will take some back and forth with multiple revisions.

Target Market(s)

Large Enterprises

Number of Pages Required

5+ page

Requirements
Must have
• Premium feel

```html
<!DOCTYPE html>
<html lang="en">
<head>
<meta charset="utf-8">
<title>Corvid Data – Users</title>
<link rel="stylesheet" href="https://fonts.googleapis.com/css2?family=Lato:wght@400;700&display=swap">
<style>
:root{
  --ink:#1f2230;
  --text:#3a3d47;
  --muted:#6b6f7a;
  --topbar:#000000;
  --sidebar:#323648;
  --sidebar-line:#5a5f74;
  --sidebar-text:#ffffff;
  --link:#3da0ee;
  --accent:#f5b31d;
  --blue:#1a7bd6;
  --page:#f1f1f2;
  --card:#ffffff;
  --line:#e1e2e5;
  --row-alt:#f3f3f4;
  --head:#f5f5f6;
}
*{box-sizing:border-box;margin:0;padding:0}
html,body{width:1200px;height:600px;overflow:hidden}
body{font-family:"Lato",sans-serif;color:var(--text);background:var(--page);position:relative;font-size:12px}
svg{display:block}

/* top bar */
.topbar{position:absolute;left:0;top:0;width:1200px;height:60px;background:var(--topbar);color:#fff}
.brand{position:absolute;left:34px;top:17px;display:flex;align-items:center;gap:8px;font-size:21px;font-weight:700;letter-spacing:-.2px}
.brand-dot{width:14px;height:14px;border-radius:50%;background:var(--accent)}
.menu-toggle{position:absolute;left:230px;top:22px}
.top-tools{position:absolute;right:26px;top:0;height:60px;display:flex;align-items:center;gap:24px}
.account{display:flex;align-items:center;gap:8px;font-size:12px}

/* sidebar */
.sidebar{position:absolute;left:0;top:60px;width:212px;height:540px;background:var(--sidebar);color:var(--sidebar-text)}
.nav-item{position:absolute;left:20px;right:23px;display:flex;align-items:center;height:18px;font-size:12px}
.nav-item .ico{width:12px;margin-right:16px;display:flex;justify-content:center}
.nav-item .chev{margin-left:auto}
.nav-item.current{color:var(--accent)}
.nav-item.sub{color:var(--link)}
.nav-item.sub .ico{color:#fff;font-size:11px}
.nav-rule{position:absolute;left:20px;right:0;border-top:1px dashed var(--sidebar-line)}
.copyright{position:absolute;left:19px;top:459px;font-size:9.5px;line-height:16px;color:#c4c7d2}
.social{position:absolute;left:20px;top:500px;display:flex;gap:14px}
.social span{width:13px;height:13px;border-radius:3px;background:#8e92a3}

/* page head */
.page-title{position:absolute;left:230px;top:82px;font-size:20px;font-weight:700;color:var(--ink)}
.btn{position:absolute;background:var(--blue);color:#fff;font-weight:700;font-size:12px;border-radius:2px;display:flex;align-items:center;justify-content:center}
.btn-add{left:294px;top:82px;width:60px;height:25px}
.search{position:absolute;left:834px;top:75px;width:244px;height:27px;display:flex;border:1px solid var(--line);background:#fff}
.search-field{flex:1;padding-left:10px;display:flex;align-items:center;font-size:10px;color:var(--muted)}
.search-go{width:32px;background:var(--accent);display:flex;align-items:center;justify-content:center}
.adv-search{position:absolute;left:1098px;top:83px;font-size:10.5px;font-weight:700;color:var(--ink);text-decoration:underline}

/* card */
.card{position:absolute;left:230px;top:117px;width:950px;height:421px;background:var(--card);border:1px solid var(--line);border-radius:5px;overflow:hidden}
.btn-edit{left:883px;top:7px;width:60px;height:25px}
.row{position:absolute;display:flex;align-items:center}
.row > div{height:100%;display:flex;align-items:center;padding-left:12px;border-right:1px solid var(--line)}
.row > div:last-child{border-right:0}
.c-x{width:37px;justify-content:center;padding-left:0!important}
.c-first{width:141px}.c-last{width:142px}.c-user{width:176px}.c-mail{width:174px}.c-stat{width:154px}
.c-act{width:111px;gap:14px;padding-left:14px!important}
.grid-head{left:8px;top:38px;width:935px;height:33px;background:var(--head);border:1px solid var(--line);border-bottom:0;border-radius:4px 4px 0 0;font-weight:700;color:var(--ink)}
.grid-head > div{justify-content:space-between;padding-right:14px}
.grid-head .sorted{background:var(--blue);color:#fff}
.open-row{left:8px;top:71px;width:935px;height:38px;border:1px solid var(--line);border-radius:0 0 4px 4px}

.perm{position:absolute;left:8px;top:113px;width:935px;height:166px;border:1px solid var(--line);border-radius:4px;overflow:hidden}
.perm-row{display:flex;height:31px;border-top:1px solid var(--line)}
.perm-row > div{display:flex;align-items:center;padding-left:14px;gap:6px}
.perm-row > div:first-child{width:584px;border-right:1px solid var(--line)}
.perm-head{height:32px;border-top:0;background:var(--head);font-weight:700;color:var(--ink)}
.perm-row.first{border-top:0;height:40px;padding-top:8px}
.box{width:11px;height:11px;border-radius:2px;background:var(--blue);display:flex;align-items:center;justify-content:center}
.perm-row .gap{margin-left:10px}
.perm-spacer{position:absolute;left:0;top:283px;width:950px;height:14px;background:var(--row-alt)}

.list-row{left:0;width:950px;height:31px;border-top:1px solid var(--line)}
.list-row .c-x{width:45px}
.list-row .c-act{width:118px}
.list-row.alt{background:var(--row-alt)}

/* pager */
.pager{position:absolute;left:626px;top:558px;height:24px;display:flex;align-items:center;gap:9px}
.page-num{width:18px;height:18px;background:var(--accent);color:#fff;font-weight:700;font-size:11px;display:flex;align-items:center;justify-content:center}
.page-size{width:49px;height:24px;border:1px solid var(--line);background:#fff;display:flex;align-items:center;justify-content:space-between;padding:0 7px;font-weight:700;color:var(--ink);margin-left:2px}
.scale{position:absolute;left:1172px;top:571px;font-size:10px;color:var(--ink)}
</style>
</head>
<body>

<header class="topbar">
  <div class="brand"><span class="brand-dot"></span>Corvid Data</div>
  <svg class="menu-toggle" width="18" height="15" viewBox="0 0 18 15"><rect y="0" width="18" height="3" fill="#fff"/><rect y="6" width="18" height="3" fill="#fff"/><rect y="12" width="18" height="3" fill="#fff"/></svg>
  <div class="top-tools">
    <svg width="21" height="14" viewBox="0 0 21 14" fill="none" stroke="#fff" stroke-width="2"><path d="M2 13a8.5 8.5 0 0 1 17 0"/><path d="M10.5 12l4-5"/></svg>
    <svg width="18" height="18" viewBox="0 0 18 18" fill="none" stroke="#fff" stroke-width="2"><path d="M2 16l10-10"/><path d="M14 1v3M16 4h-3M17 8h-2M9 2v2" stroke-width="1.5"/></svg>
    <svg width="20" height="20" viewBox="0 0 20 20"><circle cx="10" cy="10" r="10" fill="#fff"/><path d="M7 7.5a3 3 0 1 1 4 2.8c-.7.3-1 .8-1 1.5v.6" fill="none" stroke="#000" stroke-width="2.2"/><circle cx="10" cy="15.3" r="1.3" fill="#000"/></svg>
    <svg width="19" height="19" viewBox="0 0 20 20"><path fill="#fff" d="M8.6 0h2.8l.5 2.6 1.8.8 2.2-1.5 2 2-1.5 2.2.8 1.8 2.6.5v2.8l-2.6.5-.8 1.8 1.5 2.2-2 2-2.2-1.5-1.8.8-.5 2.6H8.6l-.5-2.6-1.8-.8-2.2 1.5-2-2 1.5-2.2-.8-1.8L0 11.4V8.6l2.6-.5.8-1.8-1.5-2.2 2-2 2.2 1.5 1.8-.8z"/><circle cx="10" cy="10" r="3.2" fill="#000"/></svg>
    <div class="account">Nora Vale <svg width="8" height="5" viewBox="0 0 8 5" fill="none" stroke="#fff" stroke-width="1.3"><path d="M1 1l3 3 3-3"/></svg></div>
  </div>
</header>

<nav class="sidebar">
  <div class="nav-item current" style="top:21px"><span class="ico"><svg width="10" height="11" viewBox="0 0 10 11" fill="#f5b31d"><circle cx="5" cy="3" r="3"/><path d="M0 11a5 4.5 0 0 1 10 0z"/></svg></span>User<span class="chev"><svg width="6" height="9" viewBox="0 0 6 9" fill="none" stroke="#fff" stroke-width="1.3"><path d="M1 1l3.5 3.5L1 8"/></svg></span></div>
  <div class="nav-item sub" style="top:45px"><span class="ico">»</span>Roles</div>
  <div class="nav-item sub" style="top:68px"><span class="ico">»</span>Notification Groups</div>
  <div class="nav-rule" style="top:99px"></div>
  <div class="nav-item" style="top:106px"><span class="ico"><svg width="10" height="11" viewBox="0 0 10 11" fill="#f5b31d"><ellipse cx="5" cy="2" rx="5" ry="2"/><path d="M0 3.5c0 1.1 2.2 2 5 2s5-.9 5-2V6c0 1.1-2.2 2-5 2S0 7.1 0 6z"/><path d="M0 7.5c0 1.1 2.2 2 5 2s5-.9 5-2V9c0 1.1-2.2 2-5 2S0 10.1 0 9z"/></svg></span>Date Sources</div>
  <div class="nav-item sub" style="top:129px"><span class="ico">»</span>Data Object Relationships</div>
  <div class="nav-rule" style="top:158px"></div>
  <div class="nav-item" style="top:168px"><span class="ico"><svg width="12" height="10" viewBox="0 0 12 10" fill="#f5b31d"><rect width="3" height="2"/><rect x="4.5" width="3" height="2"/><rect x="9" width="3" height="2"/><rect y="4" width="3" height="2"/><rect x="4.5" y="4" width="3" height="2"/><rect x="9" y="4" width="3" height="2"/><rect y="8" width="3" height="2"/><rect x="4.5" y="8" width="3" height="2"/><rect x="9" y="8" width="3" height="2"/></svg></span>Data Sets<span class="chev"><svg width="6" height="9" viewBox="0 0 6 9" fill="none" stroke="#fff" stroke-width="1.3"><path d="M1 1l3.5 3.5L1 8"/></svg></span></div>
  <div class="nav-rule" style="top:197px"></div>
  <div class="nav-item" style="top:205px"><span class="ico"><svg width="12" height="10" viewBox="0 0 12 10" fill="#f5b31d"><rect width="12" height="2"/><rect y="4" width="12" height="2"/><rect y="8" width="12" height="2"/></svg></span>Rule Sets</div>
  <div class="nav-rule" style="top:234px"></div>
  <div class="nav-item" style="top:244px"><span class="ico"><svg width="10" height="10" viewBox="0 0 10 10" fill="none" stroke="#f5b31d" stroke-width="1.5"><circle cx="5" cy="5" r="4"/><path d="M5 2.5V5h2"/></svg></span>Schedules</div>
  <div class="nav-rule" style="top:274px"></div>
  <div class="nav-item" style="top:282px"><span class="ico"><svg width="12" height="10" viewBox="0 0 12 10" fill="none" stroke="#f5b31d" stroke-width="1.6"><path d="M2 4a4 3 0 0 1 7.5-1M10 6a4 3 0 0 1-7.5 1"/><path d="M10 0v3H7M2 10V7h3"/></svg></span>Metadata Import/Export<span class="chev" style="margin-left:8px"><svg width="6" height="9" viewBox="0 0 6 9" fill="none" stroke="#fff" stroke-width="1.3"><path d="M1 1l3.5 3.5L1 8"/></svg></span></div>
  <div class="nav-item sub" style="top:305px"><span class="ico">»</span>Import</div>
  <div class="nav-item sub" style="top:329px"><span class="ico">»</span>Export</div>
  <p class="copyright">Copyright ©2018 Company Name.<br>&nbsp;All Rights Reserved</p>
  <div class="social" role="img" aria-label="Social network links"><span></span><span></span><span></span><span></span><span></span></div>
</nav>

<h1 class="page-title">Users</h1>
<div class="btn btn-add">Add</div>
<div class="search"><div class="search-field">Search...</div><div class="search-go"><svg width="14" height="14" viewBox="0 0 14 14" fill="none" stroke="#fff" stroke-width="2"><circle cx="6" cy="6" r="4.5"/><path d="M9.5 9.5L13 13"/></svg></div></div>
<div class="adv-search">Advanced Search</div>

<section class="card">
  <div class="btn btn-edit">Edit</div>

  <div class="row grid-head">
    <div class="c-x"></div>
    <div class="c-first sorted">First Name <svg width="7" height="11" viewBox="0 0 7 11" fill="#fff"><path d="M3.5 0L7 4H0zM3.5 11L0 7h7z"/></svg></div>
    <div class="c-last">Last Name <svg width="7" height="11" viewBox="0 0 7 11" fill="#3a3d47"><path d="M3.5 0L7 4H0zM3.5 11L0 7h7z"/></svg></div>
    <div class="c-user">Username <svg width="7" height="11" viewBox="0 0 7 11" fill="#3a3d47"><path d="M3.5 0L7 4H0zM3.5 11L0 7h7z"/></svg></div>
    <div class="c-mail">Email Address <svg width="7" height="11" viewBox="0 0 7 11" fill="#3a3d47"><path d="M3.5 0L7 4H0zM3.5 11L0 7h7z"/></svg></div>
    <div class="c-stat" style="justify-content:flex-start;gap:44px">Status <svg width="7" height="11" viewBox="0 0 7 11" fill="#3a3d47"><path d="M3.5 0L7 4H0zM3.5 11L0 7h7z"/></svg></div>
    <div class="c-act"></div>
  </div>

  <div class="row open-row">
    <div class="c-x"><svg width="10" height="6" viewBox="0 0 10 6" fill="none" stroke="#1f2230" stroke-width="1.4"><path d="M1 1l4 4 4-4"/></svg></div>
    <div class="c-first">tim</div><div class="c-last">tim</div><div class="c-user">tim.timtim</div><div class="c-mail">tim@corviddata.com</div><div class="c-stat">Active</div>
    <div class="c-act">
      <svg width="12" height="12" viewBox="0 0 12 12"><rect width="12" height="12" rx="2" fill="#1f2230"/><path d="M3 9l.5-2 4-4 1.5 1.5-4 4z" fill="#fff"/></svg>
      <svg width="13" height="13" viewBox="0 0 13 13" fill="none" stroke="#1f2230" stroke-width="1.3"><rect x="1" y="4" width="8" height="8" rx="1"/><path d="M4 4V1h8v8H9"/></svg>
      <svg width="11" height="12" viewBox="0 0 11 12" fill="#1f2230"><rect y="1.5" width="11" height="1.5"/><rect x="4" width="3" height="1.5"/><path d="M1.5 4h8l-.7 8H2.2z"/></svg>
    </div>
  </div>

  <div class="perm">
    <div class="perm-row perm-head"><div>Object</div><div>Permission</div></div>
    <div class="perm-row first"><div>System Settings</div><div><span class="box"><svg width="7" height="6" viewBox="0 0 7 6" fill="none" stroke="#fff" stroke-width="1.5"><path d="M1 3l2 2 3-4"/></svg></span>Read<span class="box gap"><svg width="7" height="6" viewBox="0 0 7 6" fill="none" stroke="#fff" stroke-width="1.5"><path d="M1 3l2 2 3-4"/></svg></span>Write</div></div>
    <div class="perm-row"><div>Users</div><div><span class="box"><svg width="7" height="6" viewBox="0 0 7 6" fill="none" stroke="#fff" stroke-width="1.5"><path d="M1 3l2 2 3-4"/></svg></span>Read<span class="box gap"><svg width="7" height="6" viewBox="0 0 7 6" fill="none" stroke="#fff" stroke-width="1.5"><path d="M1 3l2 2 3-4"/></svg></span>Write</div></div>
    <div class="perm-row"><div>Data Source</div><div>Role</div></div>
    <div class="perm-row"><div>All Data Sources</div><div>System Adminstration</div></div>
  </div>
  <div class="perm-spacer"></div>

  <div class="row list-row alt" style="top:297px">
    <div class="c-x"><svg width="10" height="6" viewBox="0 0 10 6" fill="none" stroke="#1f2230" stroke-width="1.4"><path d="M1 1l4 4 4-4"/></svg></div>
    <div class="c-first">tim</div><div class="c-last">tim</div><div class="c-user">tim.timtim</div><div class="c-mail">tim@corviddata.com</div><div class="c-stat">Active</div>
    <div class="c-act"><svg width="12" height="12" viewBox="0 0 12 12"><rect width="12" height="12" rx="2" fill="#1f2230"/><path d="M3 9l.5-2 4-4 1.5 1.5-4 4z" fill="#fff"/></svg><svg width="13" height="13" viewBox="0 0 13 13" fill="none" stroke="#1f2230" stroke-width="1.3"><rect x="1" y="4" width="8" height="8" rx="1"/><path d="M4 4V1h8v8H9"/></svg><svg width="11" height="12" viewBox="0 0 11 12" fill="#1f2230"><rect y="1.5" width="11" height="1.5"/><rect x="4" width="3" height="1.5"/><path d="M1.5 4h8l-.7 8H2.2z"/></svg></div>
  </div>
  <div class="row list-row" style="top:328px">
    <div class="c-x"><svg width="10" height="6" viewBox="0 0 10 6" fill="none" stroke="#1f2230" stroke-width="1.4"><path d="M1 1l4 4 4-4"/></svg></div>
    <div class="c-first">tim</div><div class="c-last">tim</div><div class="c-user">tim.timtim</div><div class="c-mail">tim@corviddata.com</div><div class="c-stat">Active</div>
    <div class="c-act"><svg width="12" height="12" viewBox="0 0 12 12"><rect width="12" height="12" rx="2" fill="#1f2230"/><path d="M3 9l.5-2 4-4 1.5 1.5-4 4z" fill="#fff"/></svg><svg width="13" height="13" viewBox="0 0 13 13" fill="none" stroke="#1f2230" stroke-width="1.3"><rect x="1" y="4" width="8" height="8" rx="1"/><path d="M4 4V1h8v8H9"/></svg><svg width="11" height="12" viewBox="0 0 11 12" fill="#1f2230"><rect y="1.5" width="11" height="1.5"/><rect x="4" width="3" height="1.5"/><path d="M1.5 4h8l-.7 8H2.2z"/></svg></div>
  </div>
  <div class="row list-row alt" style="top:359px">
    <div class="c-x"><svg width="10" height="6" viewBox="0 0 10 6" fill="none" stroke="#1f2230" stroke-width="1.4"><path d="M1 1l4 4 4-4"/></svg></div>
    <div class="c-first">tim</div><div class="c-last">tim</div><div class="c-user">tim.timtim</div><div class="c-mail">tim@corviddata.com</div><div class="c-stat">In Active</div>
    <div class="c-act"><svg width="12" height="12" viewBox="0 0 12 12"><rect width="12" height="12" rx="2" fill="#1f2230"/><path d="M3 9l.5-2 4-4 1.5 1.5-4 4z" fill="#fff"/></svg><svg width="13" height="13" viewBox="0 0 13 13" fill="none" stroke="#1f2230" stroke-width="1.3"><rect x="1" y="4" width="8" height="8" rx="1"/><path d="M4 4V1h8v8H9"/></svg><svg width="11" height="12" viewBox="0 0 11 12" fill="#1f2230"><rect y="1.5" width="11" height="1.5"/><rect x="4" width="3" height="1.5"/><path d="M1.5 4h8l-.7 8H2.2z"/></svg></div>
  </div>
  <div class="row list-row" style="top:390px">
    <div class="c-x"><svg width="10" height="6" viewBox="0 0 10 6" fill="none" stroke="#1f2230" stroke-width="1.4"><path d="M1 1l4 4 4-4"/></svg></div>
    <div class="c-first">tim</div><div class="c-last">tim</div><div class="c-user">tim.timtim</div><div class="c-mail">tim@corviddata.com</div><div class="c-stat">Active</div>
    <div class="c-act"><svg width="12" height="12" viewBox="0 0 12 12"><rect width="12" height="12" rx="2" fill="#1f2230"/><path d="M3 9l.5-2 4-4 1.5 1.5-4 4z" fill="#fff"/></svg><svg width="13" height="13" viewBox="0 0 13 13" fill="none" stroke="#1f2230" stroke-width="1.3"><rect x="1" y="4" width="8" height="8" rx="1"/><path d="M4 4V1h8v8H9"/></svg><svg width="11" height="12" viewBox="0 0 11 12" fill="#1f2230"><rect y="1.5" width="11" height="1.5"/><rect x="4" width="3" height="1.5"/><path d="M1.5 4h8l-.7 8H2.2z"/></svg></div>
  </div>
</section>

<div class="pager">
  <svg width="9" height="10" viewBox="0 0 9 10" fill="#1f2230"><rect width="2" height="10"/><path d="M9 0v10L3 5z"/></svg>
  <svg width="10" height="8" viewBox="0 0 10 8" fill="#1f2230"><path d="M5 0v8L0 4zM10 0v8L5 4z"/></svg>
  <span class="page-num">1</span>
  <svg width="10" height="8" viewBox="0 0 10 8" fill="#1f2230"><path d="M5 0v8L0 4zM10 0v8L5 4z"/></svg>
  <svg width="9" height="10" viewBox="0 0 9 10" fill="#1f2230"><path d="M0 0v10l6-5z"/><rect x="7" width="2" height="10"/></svg>
  <div class="page-size">20 <svg width="8" height="5" viewBox="0 0 8 5" fill="none" stroke="#1f2230" stroke-width="1.2"><path d="M1 1l3 3 3-3"/></svg></div>
</div>
<div class="scale">x10</div>

</body>
</html>
```